Graphical design for food product in 1 Liter carton

We need this design not for a real product but as a showcase for a new service.

This special situation makes it really simple for you to participate because you only have to care about how the visual impression of your design is.

Furthermore it gives you the opportunity to get an extra winning chance if you choose to also participate in the open competition at our website - where you can enter the same design as you enter here at ArtRally.

Here is the requirements:

1. You must apply your design to our attatched template

2. Make a design for a food product of your own choice, which is to be sold from retail stores in a rectangular 1 L carton – based on our template.

3. You are only allowed to use brand names and/or logos that you have the rights to use for this competition, so please make completely fictive brand names and logos.

4. Your design is evaluated on the visual impression only, which means that your text on the design can be in any language and doesn’t have to relate to the design.

5. The criteria for the evaluation of your design is your creativity, the graphical quality and how well the product will display it self in the stores.

If you also want to participate in the open competition on our website - where you can win an Lumatab Lite, and will get your design skills exposed to brand owners and packaging manufacturers all over the world, then please visit spinoframe.com/packaging-design-competition/

Attatched is:

A. Empty design template you must apply your design to. Remove the layer with our template when you return your send in your design.

B. Example of design applied to the template.

C. Example of the applied example design after it has been converted to 3D with our online 3D engine at SpinoFrame.com.

The winning design will be converted to 3D and will be used as a showcase on our website - all designers can enter their design to our open competition at SpinoFrame.com.

```html
<!DOCTYPE html>
<html lang="en">
<head>
<meta charset="utf-8">
<title>Solvane Orange Juice – 1 L Carton</title>
<link rel="stylesheet" href="https://fonts.googleapis.com/css2?family=Playfair+Display:wght@700&family=Josefin+Slab:wght@600&family=Montserrat:wght@500;700&display=swap">
<style>
  :root {
    --paper: #f7f7f7;
    --orange: #f07a3a;
    --leaf: #86c440;
    --ink-grey: #7a7a7a;
    --badge: #9a9a9a;
  }
  * { margin: 0; padding: 0; box-sizing: border-box; }
  html, body { width: 1142px; height: 1200px; overflow: hidden; background: var(--paper); }
  .carton { position: relative; width: 1142px; height: 1200px; background: var(--paper); }
  .face { position: absolute; top: 0; width: 573px; height: 1200px; }
  .face--front { left: 0; }
  .face--back { left: 573px; }

  .top-band {
    position: absolute; left: 0; top: 0; width: 288px; height: 70px;
    background: var(--orange); border-top: 9px solid var(--leaf);
  }
  .brand {
    position: absolute; left: 22px; top: 252px;
    font-family: "Montserrat", sans-serif; font-weight: 700;
    font-size: 25px; color: var(--leaf); letter-spacing: -0.5px;
  }
  .product-name {
    position: absolute; left: 20px; top: 308px;
    font-family: "Playfair Display", serif; font-weight: 700;
    font-size: 68px; line-height: 66px; color: var(--orange);
    letter-spacing: 0.5px;
  }
  .tagline {
    position: absolute; left: 22px; top: 476px;
    font-family: "Josefin Slab", serif; font-weight: 600;
    font-size: 18px; line-height: 25px; color: var(--ink-grey);
  }
  .fruit {
    position: absolute; left: 32px; top: 615px; width: 220px; height: 300px;
  }
  .fruit-art {
    position: absolute; left: 0; top: 73px; width: 220px; height: 220px;
    border-radius: 50%; background: var(--orange);
  }
  .fruit-shadow {
    position: absolute; left: 40px; top: 292px; width: 140px; height: 10px;
    border-radius: 50%; background: radial-gradient(ellipse, rgba(0,0,0,0.12), rgba(0,0,0,0));
  }
  .volume-mark {
    position: absolute; left: 234px; top: 967px; width: 32px; height: 48px;
    background: linear-gradient(180deg, #b5b5b5, var(--badge));
  }
  .tree-art {
    position: absolute; left: 313px; top: 307px; width: 237px; height: 711px;
    background: linear-gradient(180deg, rgba(134,196,64,0.35) 0%, rgba(240,122,58,0.18) 25%, rgba(134,196,64,0.12) 60%, rgba(134,196,64,0.3) 100%);
    border-radius: 40px 40px 4px 4px;
  }
  .variety {
    position: absolute; left: 444px; top: 788px;
    font-family: "Montserrat", sans-serif; font-weight: 500;
    font-size: 19px; line-height: 21px; text-transform: uppercase;
  }
  .variety .accent { color: var(--leaf); }
  .variety .main { color: var(--orange); }
</style>
</head>
<body>
<main class="carton">

  <section class="face face--front">
    <div class="top-band"></div>
    <div class="brand">Solvane</div>
    <h1 class="product-name">orange<br>juice</h1>
    <p class="tagline">Donec eu pharetra lacus<br>mollis blandit neque<br>vulputate semper</p>
    <div class="fruit">
      <div class="fruit-art" role="img" aria-label="Flat illustration of an orange with a green leaf"></div>
      <div class="fruit-shadow"></div>
    </div>
    <div class="volume-mark" role="img" aria-label="Volume badge"></div>
    <div class="tree-art" role="img" aria-label="Flat illustration of a slim orange tree with green leaves, oranges and grass at its base"></div>
    <p class="variety"><span class="accent">Tropical</span><br><span class="main">Orange<br>Juice</span></p>
  </section>

  <section class="face face--back">
    <div class="top-band"></div>
    <div class="brand">Solvane</div>
    <h2 class="product-name">orange<br>juice</h2>
    <p class="tagline">Donec eu pharetra lacus<br>mollis blandit neque<br>vulputate semper</p>
    <div class="fruit">
      <div class="fruit-art" role="img" aria-label="Flat illustration of an orange with a green leaf"></div>
      <div class="fruit-shadow"></div>
    </div>
    <div class="volume-mark" role="img" aria-label="Volume badge"></div>
    <div class="tree-art" role="img" aria-label="Flat illustration of a slim orange tree with green leaves, oranges and grass at its base"></div>
    <p class="variety"><span class="accent">Tropical</span><br><span class="main">Orange<br>Juice</span></p>
  </section>

</main>
</body>
</html>
```